Awesome photographers card for an awesome new business

Double sided business card Black background and silver logo in middle on one side. Details on otherside. please keep it simple

Industry/Entity Type

Photographer

Contact Information for Business Card

Gerald Fenwick
0452817360
GeraldFenwickPhotography47@mailbox.test
www.GeraldFenwickPhotography.test.au
Instagram _Gerald_fenwick

Requirements
Must have
• My logo in Silver
• please use instagram logo instead of "Instagram"

```html
<!DOCTYPE html>
<html lang="en">
<head>
<meta charset="utf-8">
<title>Gerald Fenwick Photography — Business Card</title>
<link href="https://fonts.googleapis.com/css2?family=Questrial&family=Roboto+Condensed:wght@700&display=swap" rel="stylesheet">
<style>
  :root {
    --page: #e6e4e0;
    --card-white: #fbfbfb;
    --band-dark: #6d6d6d;
    --band-light: #b9b9b9;
    --curve-grey: #a8a8a8;
    --name-grey: #4a4a4a;
    --contact-text: #ffffff;
    --card-black: #1f1f20;
    --silver: #c9c9c9;
    --logo-grey: #8a8a8a;
  }
  * { margin: 0; padding: 0; box-sizing: border-box; }
  html, body { width: 1200px; height: 911px; overflow: hidden; background: var(--page); }
  .canvas {
    width: 1200px; height: 911px;
    display: flex; align-items: center; justify-content: center; gap: 60px;
  }
  .card {
    width: 540px; height: 310px; border-radius: 18px; overflow: hidden; position: relative;
    box-shadow: 0 6px 18px rgba(0,0,0,0.18);
  }
  .card-front { background: var(--card-white); }
  .front-band { position: absolute; inset: 0; }
  .front-name {
    position: absolute; top: 34px; right: 44px;
    font-family: "Roboto Condensed", sans-serif; font-weight: 700;
    font-size: 19px; letter-spacing: 0.5px; color: var(--name-grey);
  }
  .front-logo {
    position: absolute; left: 28px; top: 146px; width: 96px; height: 96px;
    border: 2px solid var(--logo-grey); border-radius: 50%;
    display: flex; align-items: center; justify-content: center; text-align: center;
    font-family: "Questrial", sans-serif; font-size: 13px; line-height: 1.2;
    color: var(--logo-grey); background: var(--card-white);
  }
  .contact-list {
    position: absolute; left: 196px; top: 212px; list-style: none;
    font-family: "Questrial", sans-serif; font-size: 13px; color: var(--contact-text);
  }
  .contact-list li { display: flex; align-items: center; gap: 9px; height: 20px; }
  .contact-icon { width: 12px; height: 12px; flex: none; display: block; }
  .card-back {
    background: var(--card-black);
    display: flex; align-items: center; justify-content: center;
  }
  .back-logo {
    width: 160px; height: 160px; border: 2px solid var(--silver); border-radius: 50%;
    display: flex; align-items: center; justify-content: center; text-align: center;
    font-family: "Questrial", sans-serif; font-size: 20px; line-height: 1.3; color: var(--silver);
  }
</style>
</head>
<body>
<main class="canvas">
  <section class="card card-front" aria-label="Business card front">
    <svg class="front-band" width="540" height="310" viewBox="0 0 540 310" aria-hidden="true">
      <defs>
        <linearGradient id="bandFill" x1="0" y1="1" x2="1" y2="0">
          <stop offset="0" stop-color="#6d6d6d"/>
          <stop offset="1" stop-color="#b9b9b9"/>
        </linearGradient>
      </defs>
      <path d="M0 205 C150 205 340 160 540 60 L540 310 L0 310 Z" fill="url(#bandFill)"/>
      <path d="M0 191 C150 191 340 146 540 46" fill="none" stroke="#a8a8a8" stroke-width="3"/>
      <path d="M0 199 C150 199 340 154 540 54" fill="none" stroke="#ffffff" stroke-width="3"/>
    </svg>
    <h1 class="front-name">GERALD FENWICK</h1>
    <div class="front-logo">Gerald<br>Fenwick</div>
    <ul class="contact-list">
      <li>
        <svg class="contact-icon" viewBox="0 0 12 12" aria-hidden="true"><path d="M2 1 L4.5 1 L5.2 3.6 L3.8 4.6 C4.5 6 6 7.5 7.4 8.2 L8.4 6.8 L11 7.5 L11 10 C6 10.5 1.5 6 2 1 Z" fill="#fff"/></svg>
        0452817360
      </li>
      <li>
        <svg class="contact-icon" viewBox="0 0 12 12" aria-hidden="true"><rect x="1" y="2.5" width="10" height="7" rx="1" fill="none" stroke="#fff" stroke-width="1.2"/><path d="M1.5 3 L6 6.5 L10.5 3" fill="none" stroke="#fff" stroke-width="1.2"/></svg>
        GeraldFenwickPhotography47@mailbox.test
      </li>
      <li>
        <svg class="contact-icon" viewBox="0 0 12 12" aria-hidden="true"><circle cx="6" cy="6" r="5" fill="none" stroke="#fff" stroke-width="1.2"/><path d="M1 6 H11 M6 1 C3.5 4 3.5 8 6 11 M6 1 C8.5 4 8.5 8 6 11" fill="none" stroke="#fff" stroke-width="1"/></svg>
        www.GeraldFenwickPhotography.test.au
      </li>
      <li>
        <svg class="contact-icon" viewBox="0 0 12 12" aria-hidden="true"><rect x="1" y="1" width="10" height="10" rx="2" fill="#fff"/></svg>
        _Gerald_fenwick
      </li>
    </ul>
  </section>

  <section class="card card-back" aria-label="Business card back">
    <div class="back-logo">Gerald<br>Fenwick</div>
  </section>
</main>
</body>
</html>
```